Business Card Design Project

Tidal Oak Jobs- http:tidaloakjobs.com./janetpruitt

Industry/Entity Type

Business

Contact Information for Business Card

Well it could be a pretty color like a glossy pink look business type very Job related

```html
<!DOCTYPE html>
<html lang="en">
<head>
<meta charset="utf-8">
<title>Janet Pruitt – Business Card</title>
<link rel="stylesheet" href="https://fonts.googleapis.com/css2?family=Exo+2:wght@400;500&family=Source+Sans+3:wght@400;600&display=swap">
<style>
  :root {
    --stage: #222222;
    --paper: #ffffff;
    --gold: #f2a818;
    --ink: #231f20;
    --rule: #555555;
    --text: #1a1a1a;
  }
  * { margin: 0; padding: 0; box-sizing: border-box; }
  html, body { width: 1200px; height: 900px; overflow: hidden; }
  body { background: var(--stage); position: relative; font-family: "Source Sans 3", sans-serif; }

  .card {
    position: absolute; top: 170px; width: 347px; height: 561px;
    box-shadow: 3px 4px 6px rgba(0,0,0,0.55);
  }
  .card-front { left: 259px; background: var(--paper); }
  .card-back { left: 631px; background: var(--gold); }

  .front-mark {
    position: absolute; left: 125px; top: 97px; width: 96px; height: 96px;
    border: 5px solid var(--gold);
  }
  .front-name {
    position: absolute; left: 0; right: 0; top: 200px; text-align: center;
    font-family: "Exo 2", sans-serif; font-weight: 400; font-size: 37px;
    color: var(--ink); letter-spacing: 0.2px;
  }
  .holder-name {
    position: absolute; left: 0; right: 0; top: 324px; text-align: center;
    font-family: "Exo 2", sans-serif; font-size: 21px; color: var(--gold);
    letter-spacing: 0.6px;
  }
  .holder-rule {
    position: absolute; left: 95px; width: 158px; top: 365px; height: 1.5px;
    background: var(--rule);
  }
  .contact {
    position: absolute; left: 0; right: 0; top: 387px; text-align: center;
    font-size: 15px; line-height: 21px; color: var(--text);
  }
  .contact .label { color: var(--gold); font-weight: 600; }
  .contact .web { color: var(--gold); font-weight: 600; }

  .follow {
    position: absolute; left: 70px; right: 70px; top: 472px;
    display: flex; align-items: center; justify-content: center; gap: 6px;
    font-size: 15px; color: var(--text); letter-spacing: 0.3px;
  }
  .follow::before, .follow::after {
    content: ""; flex: 1; height: 1.5px; background: var(--gold);
  }
  .social {
    position: absolute; left: 0; right: 0; top: 507px;
    display: flex; justify-content: center; gap: 9px;
  }
  .social span { width: 23px; height: 23px; background: var(--gold); display: block; }

  .back-mark {
    position: absolute; left: 79px; top: 178px; width: 190px; height: 190px;
    border: 10px solid var(--paper);
  }
  .back-name {
    position: absolute; left: 0; right: 0; top: 392px; text-align: center;
    font-family: "Exo 2", sans-serif; font-size: 34px; color: var(--paper);
  }
</style>
</head>
<body>
  <section class="card card-front">
    <div class="front-mark"></div>
    <div class="front-name">Janet Pruitt</div>
    <div class="holder-name">JANET PRUITT</div>
    <div class="holder-rule"></div>
    <div class="contact">
      <div><span class="label">P:</span> 555-204-7731</div>
      <div><span class="label">E:</span> hello@tidaloakjobs.com</div>
      <div class="web">www.tidaloakjobs.com</div>
    </div>
    <div class="follow">FOLLOW US ON</div>
    <div class="social"><span></span><span></span><span></span><span></span></div>
  </section>

  <section class="card card-back">
    <div class="back-mark"></div>
    <div class="back-name">Janet Pruitt</div>
  </section>
</body>
</html>
```